Website Redesign Project Puzzle Vault Larkfield

We are an escape room company located in Ashburn, Virginia. We currently have a website https://www.puzzlevaultlarkfield.example based upon html/bootstrap/javascript/php/mysql and I'd like to keep it that way. I'm looking for someone upgrade the front page so it is more informative, cleaner, quicker to load, and optimizes the space for full sale opportunities.

Target Market(s)

Corporate Clients, Families, Friends. All ages

Industry/Entity Type

Entertainment Industry

Coding

Coded - Design and coding required

Number of Pages Required

3 page

Font styles to use
Other font styles liked:
• Similar to Friendboard or Amazon

Requirements
Must have
• Must be mobile friendly. bootstrap. Lots of graphics (will provide) nice and easy to read fonts. Easy to read layout. Must look clean, fresh, exciting, and want to grab attention.
• Please visit my facebook page and website for more details. facebook.com/puzzlevaultlarkfield
Nice to have
• Same color as existing but open to options if they look nice.
Should not have
• Should not be wordpress or hard to modify.

```html
<!DOCTYPE html>
<html lang="en">
<head>
<meta charset="utf-8">
<title>Puzzle Vault Larkfield — Escape Rooms</title>
<link href="https://fonts.googleapis.com/css2?family=Fredoka:wght@400;500;600&family=Lato:wght@400;700&display=swap" rel="stylesheet">
<style>
:root{
  --blue:#1596e6;
  --ink:#1b1b1b;
  --text:#555;
  --light:#f1f1f1;
  --field:#ececec;
  --footer:#1c1c1c;
  --white:#fff;
}
*{box-sizing:border-box;margin:0;padding:0}
html,body{width:1200px;height:5186px;overflow:hidden}
body{position:relative;background:var(--white);font-family:"Lato",sans-serif;color:var(--text)}
.abs{position:absolute}
h1,h2,h3{font-family:"Fredoka",sans-serif;font-weight:500}

/* hero */
.hero{left:0;top:0;width:1200px;height:725px;background:linear-gradient(160deg,#2a1b5e 0%,#6a1d55 40%,#c8466a 60%,#3a1f4e 100%)}
.hero-curve{left:0;top:480px}
.brand{left:110px;top:18px;display:flex;align-items:center;gap:10px;font-family:"Fredoka",sans-serif;font-weight:600;color:var(--blue);font-size:26px;line-height:1}
.brand-mark{width:34px;height:34px;background:var(--blue)}
.phone{left:732px;top:22px;display:flex;align-items:center;gap:12px;color:var(--white);font-weight:700;font-size:18px}
.phone-icon{width:34px;height:34px;background:var(--white);border-radius:6px;display:flex;align-items:center;justify-content:center}
.btn-book{left:954px;top:16px;width:132px;height:40px;background:var(--blue);color:var(--white);font-size:18px;display:flex;align-items:center;justify-content:center}
.nav{left:473px;top:78px;display:flex;gap:32px;color:var(--white);font-size:15px}
.hero-title{left:0;top:360px;width:1200px;text-align:center;color:var(--white);font-size:92px;font-weight:600;letter-spacing:1px}

/* rooms */
.room{top:840px;width:232px;height:262px;color:var(--white);display:flex;flex-direction:column;align-items:center;justify-content:center;text-align:center}
.room .level{font-size:14px;font-weight:700}
.room .name{font-family:"Fredoka",sans-serif;font-size:30px;font-weight:500;margin-top:4px}
.room.candy{background:linear-gradient(180deg,#9a3b45,#5b6e88)}
.room.bank{background:linear-gradient(180deg,#444,#1f1f1f)}
.room.jail{background:linear-gradient(180deg,#8a4a2e,#d0561f)}
.room.active{background:var(--blue)}
.room.active .desc{font-size:13px;line-height:24px;padding:6px 18px 8px}
.room .btn-outline{border:2px solid var(--white);width:144px;height:42px;display:flex;align-items:center;justify-content:center;font-size:16px;font-weight:700}

.band-grey{left:0;top:1188px;width:1200px;height:162px;background:var(--light)}
.section-title{left:0;width:1200px;text-align:center;color:var(--ink);font-size:46px}
.section-title.on-blue{color:var(--white)}
.corp-photo{left:0;top:1350px;width:1200px;height:593px;background:linear-gradient(120deg,#3c5d7a 0%,#8a7f78 45%,#c9a48d 60%,#2d4e78 100%)}

/* packages */
.packages{left:0;top:1943px;width:1200px;height:1157px;background:linear-gradient(180deg,#f1f1f1,#fafafa)}
.pkg{background:var(--white);box-shadow:0 4px 12px rgba(0,0,0,.15);text-align:center}
.pkg-head{background:#111;color:var(--white);font-family:"Fredoka",sans-serif;font-size:22px;display:flex;align-items:center;justify-content:center;line-height:1.4}
.pkg.featured .pkg-head{background:var(--blue)}
.pkg .sub{font-size:18px;color:#444}
.pkg .big{font-size:22px;color:#444;margin-top:4px}
.pkg ul{list-style:none;margin:14px auto 0;width:150px;text-align:left;font-size:15px;line-height:27px}
.pkg li::before{content:"» ";color:var(--blue);font-weight:700}
.pkg .btn{margin:12px auto 0;width:160px;height:48px;border:2px solid #111;display:flex;align-items:center;justify-content:center;font-weight:700;font-size:17px;color:#111}
.pkg.featured .btn{background:var(--blue);border-color:var(--blue);color:var(--white)}

.field{background:var(--field);border-bottom:2px solid #ddd;padding:0 38px;display:flex;align-items:center;font-size:16px;color:#444}
.field.area{align-items:flex-start;padding-top:22px}
.field.on-blue{background:var(--white);border:none}
.field .caret{margin-left:auto;width:0;height:0;border-left:7px solid transparent;border-right:7px solid transparent;border-top:10px solid #999}
.submit{background:var(--blue);color:var(--white);font-weight:700;font-size:19px;display:flex;align-items:center;justify-content:center}

/* birthday */
.birthday{left:0;top:3100px;width:1200px;height:1144px;background:var(--blue)}
.lead{left:230px;width:740px;text-align:center;color:var(--white);font-size:15px;line-height:31px}
.price{outline:2px solid var(--white);outline-offset:3px;background:var(--white);text-align:center;padding-top:28px}
.price .inner{position:absolute;inset:4px;border:2px solid var(--blue)}
.price h3{position:relative;color:var(--blue);font-size:30px}
.price p{position:relative;font-size:13px;line-height:24px;color:#555;margin:10px auto 0;width:300px}
.note-title{left:264px;top:3595px;font-size:33px;color:var(--white)}
.note-text{left:268px;top:3650px;color:var(--white);font-size:17px}
.submit-outline{border:2px solid var(--white);color:var(--white);font-weight:700;font-size:19px;display:flex;align-items:center;justify-content:center}

/* how it works */
.how{left:0;top:4244px;width:1200px;height:577px;background:var(--light)}
.how-lead{left:200px;top:4400px;width:800px;text-align:center;font-size:15px;line-height:31px;color:#555}
.faq{left:113px;width:402px;height:48px;background:var(--white);border:1px solid #e2e2e2;padding-left:20px;display:flex;align-items:center;font-size:16px;color:#555}
.faq.open{background:var(--blue);color:var(--white);border-color:var(--blue)}
.answer{left:537px;top:4515px;width:550px;height:226px;background:var(--white);padding:28px 30px;font-size:13px;line-height:29px;color:#666}

/* footer */
.footer{left:0;top:4821px;width:1200px;height:365px;background:var(--footer)}
.f-col{top:4870px;font-size:13px;line-height:30px;color:#ddd}
.f-col h4{font-family:"Fredoka",sans-serif;font-weight:500;font-size:19px;color:var(--white);margin-bottom:20px}
.f-item{display:flex;gap:16px;margin-bottom:14px;line-height:24px}
.f-item svg{flex:none;margin-top:4px}
.social{display:flex;align-items:center;gap:14px;margin-bottom:20px}
.social .dot{width:28px;height:28px;border-radius:50%;background:var(--blue)}
.copy{left:0;top:5140px;width:1200px;text-align:center;font-size:13px;color:#ddd}
</style>
</head>
<body>

<div class="abs hero" role="img" aria-label="Photo of a group of smiling players inside an escape room holding a trophy"></div>
<svg class="abs hero-curve" width="1200" height="270" viewBox="0 0 1200 270">
  <path d="M0 120 Q600 340 1200 40 L1200 270 L0 270 Z" fill="#fff"/>
  <path d="M130 162 Q600 330 1060 150 Q600 290 130 162 Z" fill="#1596e6"/>
</svg>
<div class="abs brand"><span class="brand-mark"></span>Puzzle Vault Larkfield</div>
<div class="abs phone">
  <span class="phone-icon"><svg width="18" height="18" viewBox="0 0 24 24"><path d="M6.6 10.8a15 15 0 0 0 6.6 6.6l2.2-2.2c.3-.3.7-.4 1-.2 1.1.4 2.3.6 3.6.6.6 0 1 .4 1 1V20c0 .6-.4 1-1 1A17 17 0 0 1 3 4c0-.6.4-1 1-1h3.5c.6 0 1 .4 1 1 0 1.3.2 2.5.6 3.6.1.3 0 .7-.2 1z" fill="#111"/></svg></span>
  (555) 014-7731
</div>
<div class="abs btn-book">Book Now</div>
<nav class="abs nav"><span>Escape Rooms</span><span>Special Events</span><span>Locations</span><span>How It Works</span><span>Contact Us</span></nav>
<h1 class="abs hero-title">ESCAPE ROOMS</h1>

<div class="abs room candy" style="left:111px" role="img" aria-label="Candy Shop room photo"><div class="level">Difficulty: 7/10</div><div class="name">Candy Shop</div></div>
<div class="abs room active" style="left:360px">
  <div class="level">Difficulty: 10/10</div><div class="name">Elevator</div>
  <div class="desc">Description: The main elevators are down so you'll need to take the freight elevator to the top floor if you</div>
  <div class="btn-outline">BOOK NOW</div>
</div>
<div class="abs room bank" style="left:608px" role="img" aria-label="Bank Heist room photo"><div class="level">Difficulty: 8/10</div><div class="name">Bank Heist</div></div>
<div class="abs room jail" style="left:856px" role="img" aria-label="Jail Break room photo"><div class="level">Difficulty: 8/10</div><div class="name">Jail Break</div></div>

<div class="abs band-grey"></div>
<h2 class="abs section-title" style="top:1250px">Corporate Events</h2>
<div class="abs corp-photo" role="img" aria-label="Large group photo of guests posing in the escape room lobby"></div>

<div class="abs packages"></div>
<h2 class="abs section-title" style="top:2005px">Three Packages Offered</h2>

<div class="abs pkg" style="left:177px;top:2158px;width:284px;height:302px">
  <div class="pkg-head" style="height:82px">On-site multi-room</div>
  <div style="padding-top:28px"><div class="sub">single hour</div><div class="big">up to 30 people</div>
  <ul><li>Nemo enim ipsam</li><li>Nemo enim ipsam</li><li>Nemo enim ipsam</li></ul>
  <div class="btn">Buy Now</div></div>
</div>
<div class="abs pkg featured" style="left:469px;top:2114px;width:262px;height:398px">
  <div class="pkg-head" style="height:112px">Off-site Hot Seat<br>Escape Room</div>
  <div style="padding-top:22px"><div class="sub">Number of Players</div><div class="big">20 to 100 people</div>
  <ul><li>Nemo enim ipsam</li><li>Nemo enim ipsam</li><li>Nemo enim ipsam</li><li>Nemo enim ipsam</li><li>Nemo enim ipsam</li></ul>
  <div class="btn">Buy Now</div></div>
</div>
<div class="abs pkg" style="left:759px;top:2158px;width:264px;height:302px">
  <div class="pkg-head" style="height:82px">Off-site Customer<br>Escape Room</div>
  <div style="padding-top:22px"><div class="sub">Number of Players</div><div class="big">30+ people</div>
  <ul><li>Nemo enim ipsam</li><li>Nemo enim ipsam</li><li>Nemo enim ipsam</li></ul>
  <div class="btn">Buy Now</div></div>
</div>

<div class="abs field" style="left:197px;top:2682px;width:393px;height:64px">Name</div>
<div class="abs field" style="left:610px;top:2682px;width:390px;height:64px">Email</div>
<div class="abs field" style="left:197px;top:2758px;width:393px;height:64px">Select a package<span class="caret"></span></div>
<div class="abs field" style="left:610px;top:2758px;width:390px;height:64px">Phone Number</div>
<div class="abs field area" style="left:197px;top:2838px;width:803px;height:102px">brief description</div>
<div class="abs submit" style="left:823px;top:2959px;width:177px;height:57px">Submit</div>

<div class="abs birthday"></div>
<h2 class="abs section-title on-blue" style="top:3165px">Birthday Parties</h2>
<p class="abs lead" style="top:3244px">Celebrate this year in style by treating your family with an escape room birthday package. You and your loved ones have the choice of four escape rooms and will enjoy a private party afterwards in our party room. Either of these packages will be sure to satisfy your needs.</p>
<div class="abs price" style="left:177px;top:3378px;width:403px;height:165px"><span class="inner"></span><h3>Just $150</h3><p>A private escape room event with party room pizza and soda</p></div>
<div class="abs price" style="left:619px;top:3378px;width:404px;height:165px"><span class="inner"></span><h3>Just $125</h3><p>A private escape room event with a party room rental</p></div>
<h3 class="abs note-title">Note:</h3>
<p class="abs note-text">A $50 cleaning fee applies to all parties who don't clean after themselves</p>
<h2 class="abs section-title on-blue" style="top:3724px">Contact Form</h2>
<div class="abs field on-blue" style="left:197px;top:3825px;width:393px;height:64px">Name</div>
<div class="abs field on-blue" style="left:610px;top:3825px;width:390px;height:64px">Email</div>
<div class="abs field on-blue" style="left:197px;top:3901px;width:393px;height:64px">Package<span class="caret"></span></div>
<div class="abs field on-blue" style="left:610px;top:3901px;width:390px;height:64px">Phone Number</div>
<div class="abs field area on-blue" style="left:197px;top:3978px;width:803px;height:100px">Description</div>
<div class="abs submit-outline" style="left:197px;top:4103px;width:177px;height:57px">Submit</div>

<div class="abs how"></div>
<h2 class="abs section-title" style="top:4306px">How It Works</h2>
<p class="abs how-lead">An escape room is a themed environment where you and your friends must work together to complete the objectives through solving puzzles before time runs out. Most missions will lock you in while some of our missions do not.</p>
<div class="abs faq open" style="top:4515px">How do I make a reservation?</div>
<div class="abs faq" style="top:4575px">How long does an escape last?</div>
<div class="abs faq" style="top:4635px">Is there an age limit?</div>
<div class="abs faq" style="top:4694px">I'm pregnant, can I participate?</div>
<div class="abs answer">Nemo enim ipsam voluptatem quia voluptas sit aspernatur aut odit aut fugit, sed quia consequuntur magni dolores eos qui ratione voluptatem sequi nesciunt. Neque porro quisquam est, qui dolorem ipsum quia dolor sit amet, consectetur, adipisci velit, sed quia non numquam eius modi tempora incidunt ut labore et dolore magnam aliquam quaerat voluptatem.</div>

<div class="abs footer"></div>
<div class="abs f-col" style="left:113px;width:300px">
  <h4>Contact Us</h4>
  <div class="f-item"><svg width="14" height="18" viewBox="0 0 14 18"><path d="M7 0a7 7 0 0 0-7 7c0 5 7 11 7 11s7-6 7-11a7 7 0 0 0-7-7zm0 10a3 3 0 1 1 0-6 3 3 0 0 1 0 6z" fill="#fff"/></svg><span>1180 Fenwick Lane, Suite 12,<br>Larkfield, Va 20100</span></div>
  <div class="f-item"><svg width="16" height="16" viewBox="0 0 24 24"><path d="M6.6 10.8a15 15 0 0 0 6.6 6.6l2.2-2.2c.3-.3.7-.4 1-.2 1.1.4 2.3.6 3.6.6.6 0 1 .4 1 1V20c0 .6-.4 1-1 1A17 17 0 0 1 3 4c0-.6.4-1 1-1h3.5c.6 0 1 .4 1 1 0 1.3.2 2.5.6 3.6.1.3 0 .7-.2 1z" fill="#fff"/></svg><span>Phone:<br>&nbsp;(555) 014 7731</span></div>
  <div class="f-item"><svg width="16" height="12" viewBox="0 0 16 12"><rect width="16" height="12" fill="#fff"/><path d="M0 0l8 6 8-6" stroke="#1c1c1c" stroke-width="1.5" fill="none"/></svg><span>Email:<br>sales@puzzlevaultlarkfield.example</span></div>
</div>
<div class="abs f-col" style="left:461px;width:200px">
  <h4>Hours</h4>
  Wednesday - Fridays<br>(4 to 10pm)<br>Weekends<br>(11am to 9pm)
</div>
<div class="abs f-col" style="left:684px;width:200px">
  <h4>Quick Links</h4>
  Escape Rooms<br>Special Events<br>Locations<br>How It Works<br>Contact Us
</div>
<div class="abs f-col" style="left:910px;width:200px">
  <h4>Connect With us</h4>
  <div class="social"><span class="dot"></span>Friendboard</div>
  <div class="social"><span class="dot"></span>Chirpline</div>
  <div class="social"><span class="dot"></span>Worknet</div>
</div>
<div class="abs copy">Copyrights @ 2019 All Rights Reserved</div>

</body>
</html>
```